Luxury Wine Label for New Startup Winery

We need a wine label for our new winery startup. We have worked with a local designer but do not feel the resulting label / logo have the elevation required to present our brand as a luxury wine. Our winery is called "Quailbrook Vineyards" and we are focused on extremely high quality hand crafted artisan and estate wines from the Pacific Northwest.
We would like to see designs that utilize a tree line, or other imagery that represents the "Quailbrook" part of our company name. Another interesting feature could be wood grain.
A logo will be required based on your design so please design with this in mind:
This logo should be consistent with the wine bottle label design, and should be representative of our high end exclusive wine while giving a sense of place (Oregon/ Pacific Northwest.)
I will supply an image of the design we received from our local designer, PLEASE NOTE: in general we do like wood grain and tree line concepts but feel the execution was poorly done.
ATTN: Logo design should be suitable for use on: Bottles (Red wine/rose/white wine), Bussiness cards, vehicle signage, business signage, etc
P.S.:
If you have a design that is not outside the box we are still interested in seeing it.
Label is for a burgundy style bottle with a label height of 3.5 - 4" and a width of 3.5-4"
any label <= 4"x4" and >=3.5"x3.5" will be acceptable:
HOWEVER Width should be greater than or equal to height due to the bottle format
Target Market(s)
Wine enthusiasts with adequate discretionary budgets to afford $100 bottles of wine.
Industry/Entity Type
Wine / Winery
Requirements
Must have
- A sense of luxury, a feel of exclusivity, and a theme consistent with our product and brand name
Nice to have
- Tree line, wood grain or other wood themes. Serif fonts
Should not have
- anything cheesy, off topic, hard to read script fonts or anything that makes the label hard to read from a few feet away or too busy

```html
<!DOCTYPE html>
<html lang="en">
<head>
<meta charset="utf-8">
<title>Quailbrook Vineyards — Wine Label</title>
<link rel="stylesheet" href="https://fonts.googleapis.com/css2?family=Cormorant+Garamond:wght@400;500&display=swap">
<style>
  :root {
    --backdrop: #262c35;
    --label-paper: #2e3136;
    --label-paper-light: #55585d;
    --gold: #b99a68;
    --gold-light: #d6bc8c;
    --silver: #b9bcc2;
    --silver-dark: #7d8188;
  }
  * { box-sizing: border-box; margin: 0; padding: 0; }
  html, body {
    width: 1200px;
    height: 860px;
    overflow: hidden;
    background: var(--backdrop);
  }
  .canvas {
    position: relative;
    width: 1200px;
    height: 860px;
    display: flex;
    align-items: center;
    justify-content: center;
  }
  .wine-label {
    position: relative;
    width: 760px;
    height: 720px;
    background: radial-gradient(ellipse at 60% 40%, var(--label-paper-light) 0%, var(--label-paper) 70%);
    overflow: hidden;
  }
  .treeline {
    position: absolute;
    left: 0;
    width: 100%;
    height: 120px;
  }
  .treeline--upper {
    top: 0;
    background: linear-gradient(90deg, var(--gold) 0%, var(--gold-light) 30%, var(--silver) 55%, var(--silver-dark) 100%);
    opacity: 0.85;
  }
  .treeline--lower {
    bottom: 0;
    background: linear-gradient(90deg, var(--silver-dark) 0%, var(--gold) 40%, var(--gold-light) 65%, var(--silver) 100%);
    opacity: 0.85;
  }
  .label-art {
    position: absolute;
    inset: 0;
  }
  .vintage {
    font-family: "Cormorant Garamond", serif;
    font-size: 40px;
    font-weight: 400;
    fill: var(--gold);
    letter-spacing: 2px;
  }
  .brand-name {
    font-family: "Cormorant Garamond", serif;
    font-size: 44px;
    font-weight: 500;
    fill: var(--gold-light);
    letter-spacing: 12px;
  }
  .brand-sub {
    font-family: "Cormorant Garamond", serif;
    font-size: 24px;
    font-weight: 500;
    fill: var(--gold-light);
    letter-spacing: 14px;
  }
  .region {
    font-family: "Cormorant Garamond", serif;
    font-size: 20px;
    font-weight: 500;
    fill: var(--gold);
    letter-spacing: 10px;
  }
  .frame-ring { fill: none; stroke: var(--gold); stroke-width: 1.5; }
  .brand-dot { fill: none; stroke: var(--silver); stroke-width: 2; }
</style>
</head>
<body>
<div class="canvas">
  <div class="wine-label">
    <div class="treeline treeline--upper" role="img" aria-label="Silhouetted evergreen tree line in gold and silver foil along the top edge"></div>
    <div class="treeline treeline--lower" role="img" aria-label="Mirrored evergreen tree line in gold and silver foil along the bottom edge"></div>

    <svg class="label-art" width="760" height="720" viewBox="0 0 760 720">
      <defs>
        <path id="region-arc" d="M 180 360 A 200 200 0 0 0 580 360"/>
      </defs>
      <circle class="frame-ring" cx="380" cy="360" r="235"/>

      <text class="vintage" x="380" y="215" text-anchor="middle">2025</text>

      <circle class="brand-dot" cx="380" cy="272" r="16"/>

      <text class="brand-name" x="386" y="360" text-anchor="middle">QUAILBROOK</text>
      <text class="brand-sub" x="387" y="402" text-anchor="middle">VINEYARDS</text>

      <text class="region">
        <textPath href="#region-arc" startOffset="50%" text-anchor="middle">PACIFIC NORTHWEST</textPath>
      </text>
    </svg>
  </div>
</div>
</body>
</html>
```